New stationary design for online film company

We need some new stationary to fit with our new logo. The stationary should be professional, clean and simple.
We need designs for a full set of business stationary.
We need - letterhead, envelopes, invoices, proposals, coverslip/note and cover page

Industry/Entity Type

Business

```html
<!DOCTYPE html>
<html lang="en">
<head>
<meta charset="utf-8">
<title>framewelltv stationery set</title>
<link href="https://fonts.googleapis.com/css2?family=Montserrat:wght@400;500;600;700&display=swap" rel="stylesheet">
<style>
:root{
  --navy:#0b4a73;
  --sky:#6aa6c0;
  --mist:#e7ecf2;
  --paper:#ffffff;
  --ink:#333b44;
  --backdrop:#d9d6d2;
}
*{box-sizing:border-box;margin:0;padding:0}
html,body{width:1200px;height:757px;overflow:hidden}
body{background:var(--backdrop);font-family:"Montserrat",sans-serif;color:var(--ink);position:relative}
.sheet{position:absolute;background:var(--paper);overflow:hidden;box-shadow:0 2px 6px rgba(0,0,0,.18)}
.wordmark{display:flex;align-items:center;gap:6px;font-weight:600;color:var(--navy);letter-spacing:-.5px;white-space:nowrap}
.wordmark .dot{border-radius:50%;background:var(--navy);flex:none}
.wordmark.light{color:#fff}
.wordmark.light .dot{background:#fff}
.wave{position:absolute;left:0;bottom:0;width:100%;display:block}
.web{position:absolute;right:22px;color:#fff;letter-spacing:2px;font-weight:500}

/* letterhead */
.letterhead{left:11px;top:20px;width:509px;height:718px}
.letterhead .wordmark{position:absolute;left:36px;top:36px;font-size:28px;gap:8px}
.letterhead .wordmark .dot{width:26px;height:26px}
.contact{position:absolute;border-left:1px solid #c9ced4;padding-left:6px;font-size:5.5px;line-height:1.75;color:#444}
.letterhead .contact{left:428px;top:18px}
.contact .gap{margin-top:3px}
.watermark{position:absolute;border-radius:50%;background:var(--mist)}
.letterhead .watermark{left:150px;top:300px;width:220px;height:220px}
.letterhead .wave{height:60px}
.letterhead .web{bottom:14px;font-size:8px}

/* business cards */
.card{top:21px;width:216px;height:123px}
.card-front{left:575px;background:var(--navy)}
.card-front .wordmark{position:absolute;left:0;right:0;top:44px;justify-content:center;font-size:20px}
.card-front .wordmark .dot{width:16px;height:16px}
.card-front .web{left:0;right:0;text-align:center;bottom:8px;font-size:5.5px}
.card-back{left:810px}
.card-back .wordmark{position:absolute;left:22px;top:50px;font-size:14px;gap:4px}
.card-back .wordmark .dot{width:13px;height:13px}
.card-back .contact{left:125px;top:16px;font-size:5px;line-height:1.8}
.card-back .person{font-size:7.5px;font-weight:700;color:var(--navy);line-height:1.1}
.card-back .role{font-size:5.5px;color:var(--sky);margin-bottom:4px}
.card-back .wave{height:30px}
.card-back .web{bottom:6px;right:6px;font-size:5px;letter-spacing:1px}

/* envelope backs */
.env-back-a{left:571px;top:158px;width:585px;height:200px}
.env-back-b{left:559px;top:350px;width:585px;height:262px;border:1px solid #777}
.flap{position:absolute;left:0;top:0;width:100%;display:block}
.flap-mark{position:absolute;left:0;right:0;justify-content:center;font-size:16px}
.flap-mark .dot{width:14px;height:14px}

/* envelope front */
.env-front{left:601px;top:453px;width:585px;height:262px}
.env-front .wordmark{position:absolute;left:26px;top:22px;font-size:26px;gap:7px}
.env-front .wordmark .dot{width:26px;height:26px}
.env-front .address{position:absolute;left:26px;top:72px;font-size:8.5px;letter-spacing:.8px;color:#333}
.env-front .watermark{right:20px;top:130px;width:56px;height:56px}
.env-front .wave{height:52px}
.env-front .web{bottom:16px;font-size:7.5px}
</style>
</head>
<body>

<section class="sheet letterhead" aria-label="Letterhead">
  <div class="wordmark"><span class="dot"></span>framewelltv</div>
  <div class="contact">
    <div>&#9990; 123-456-7890</div>
    <div>&#9993; info@framewelltv.com</div>
    <div class="gap">00, Complex Name</div>
    <div>street, city 000452</div>
  </div>
  <div class="watermark" aria-hidden="true"></div>
  <svg class="wave" viewBox="0 0 509 60" preserveAspectRatio="none" aria-hidden="true">
    <path d="M0 22 C120 50 300 40 509 22" fill="none" stroke="var(--sky)" stroke-width="2.5"/>
    <path d="M0 28 C140 60 320 40 509 28 L509 60 L0 60 Z" fill="var(--navy)"/>
  </svg>
  <div class="web">www.framewelltv.com</div>
</section>

<section class="sheet card card-front" aria-label="Business card front">
  <div class="wordmark light"><span class="dot"></span>framewelltv</div>
  <div class="web">www.framewelltv.com</div>
</section>

<section class="sheet card card-back" aria-label="Business card back">
  <div class="wordmark"><span class="dot"></span>framewelltv</div>
  <div class="contact">
    <div class="person">Your Name</div>
    <div class="role">Designation</div>
    <div>&#9990; 123-456-7890</div>
    <div>&#9743; 123-456-7890</div>
    <div>&#9993; info@framewelltv.com</div>
    <div class="gap">00, Complex Name</div>
    <div>street, city 000452</div>
  </div>
  <svg class="wave" viewBox="0 0 216 30" preserveAspectRatio="none" aria-hidden="true">
    <path d="M0 8 C60 26 140 22 216 6" fill="none" stroke="var(--sky)" stroke-width="1.5"/>
    <path d="M0 12 C60 32 150 22 216 10 L216 30 L0 30 Z" fill="var(--navy)"/>
  </svg>
  <div class="web">www.framewelltv.com</div>
</section>

<section class="sheet env-back-a" aria-label="Envelope back, two flap colours">
  <svg class="flap" viewBox="0 0 585 200" aria-hidden="true">
    <path d="M0 0 H585 L575 20 Q560 60 520 70 L430 80 H155 L65 70 Q25 60 10 20 Z" fill="var(--sky)"/>
    <path d="M0 80 H585 L575 100 Q560 140 520 150 L320 180 Q292 186 265 180 L65 150 Q25 140 10 100 Z" fill="var(--navy)"/>
  </svg>
  <div class="wordmark light flap-mark" style="top:30px"><span class="dot"></span>framewelltv</div>
  <div class="wordmark light flap-mark" style="top:118px"><span class="dot"></span>framewelltv</div>
</section>

<section class="sheet env-back-b" aria-label="Envelope back, white">
  <svg class="flap" viewBox="0 0 585 110" aria-hidden="true">
    <path d="M0 0 Q4 28 30 34 L270 100 Q292 106 314 100 L560 34 Q580 28 585 0" fill="none" stroke="#555" stroke-width="1"/>
  </svg>
  <div class="wordmark flap-mark" style="top:50px"><span class="dot"></span>framewelltv</div>
</section>

<section class="sheet env-front" aria-label="Envelope front">
  <div class="wordmark"><span class="dot"></span>framewelltv</div>
  <div class="address">00, Complex Name, street, city 000452</div>
  <div class="watermark" aria-hidden="true"></div>
  <svg class="wave" viewBox="0 0 585 52" preserveAspectRatio="none" aria-hidden="true">
    <path d="M0 4 C160 36 380 34 585 2" fill="none" stroke="var(--sky)" stroke-width="2.5"/>
    <path d="M0 10 C170 44 390 30 585 8 L585 52 L0 52 Z" fill="var(--navy)"/>
  </svg>
  <div class="web">www.framewelltv.com</div>
</section>

</body>
</html>
```